Storm Restoration Contractor needs a professional letterhead design

Looking for a professional letterhead design. Not looking for your cheapo MS Word standard ones that are readily available. Dont want it to be cookie cutter look like ones readily available online. We just recently changed our logo and want to freshen up all our documents. Our company handles restoring a property back to a pre-loss condition after a storm damages it. For example, wind, hail, flood, fire losses.

Target Market(s)

Property Owners, Homeowners, Property Owners, Commercial Property Owners, Property Management Companies

Industry/Entity Type

Construction Company

Requirements
Must have
• Professional, Use 1 of 2 logo options
• Storm Restoration, Roofing, Siding, Windows

```html
<!DOCTYPE html>
<html lang="en">
<head>
<meta charset="utf-8">
<title>Stormline Exteriors Letterhead</title>
<link href="https://fonts.googleapis.com/css2?family=Open+Sans:wght@400;600;700&display=swap" rel="stylesheet">
<style>
  :root {
    --backdrop: #e6e7e9;
    --paper: #ffffff;
    --brand-blue: #1976c2;
    --ink: #3a3a3a;
  }
  * { box-sizing: border-box; margin: 0; padding: 0; }
  html, body {
    width: 1200px; height: 1200px; overflow: hidden;
    background: var(--backdrop);
    font-family: "Open Sans", sans-serif;
  }
  .letterhead {
    position: absolute; left: 200px; top: 50px;
    width: 800px; height: 1100px;
    background: var(--paper);
  }
  .brand {
    position: absolute; left: 50px; top: 58px;
    display: flex; align-items: center; gap: 12px;
  }
  .brand-dot {
    width: 60px; height: 60px; border-radius: 50%;
    background: var(--brand-blue);
  }
  .brand-name {
    color: var(--brand-blue);
    font-weight: 700; font-size: 30px; line-height: 1.05;
    letter-spacing: 0.5px; text-transform: uppercase;
  }
  .contact {
    position: absolute; right: 49px; top: 88px;
    text-align: right; color: var(--ink);
    font-size: 12px; line-height: 19px;
  }
  .contact .label { font-weight: 600; color: var(--brand-blue); }
  .contact .item + .item { margin-left: 8px; }
  .footer-bar {
    position: absolute; left: 0; right: 0; bottom: 0;
    height: 11px; background: var(--brand-blue);
  }
</style>
</head>
<body>
  <main class="letterhead">
    <header>
      <div class="brand">
        <span class="brand-dot"></span>
        <div class="brand-name">Stormline<br>Exteriors</div>
      </div>
      <address class="contact" style="font-style:normal">
        <div>1250 Harbor Ridge Rd Ste 210, Lakeview, MD 20900</div>
        <div>
          <span class="item"><span class="label">P:</span> 555-014-2390</span>
          <span class="item"><span class="label">F:</span> 555-014-2391</span>
          <span class="item"><span class="label">W:</span> www.stormlinepro.com</span>
        </div>
      </address>
    </header>
    <div class="footer-bar"></div>
  </main>
</body>
</html>
```